Two Versions of a Business Card for a Lawyer

Summary: I need a logo and a business card. The business card is two-sided and comes in two versions. One version is conservative, the other is slightly different with one or more pink embellishments in the logo or somewhere else in the business card.
I'm about to start off as a sole practitioner in criminal and immigration law. I'll largely be working with marginalised communities and in areas of social justice. One of my main focuses will be gendered violence, I'm hoping to specialise my practice towards representing victims of domestic and sexual violence and sex workers. I want a business card which would attract this clientele and make them feel safe to speak with me. I'd also like it to communicate a sense of hope.
However, the business card still has to be very conservative as the legal profession is very stuffy. So I was thinking of having two versions of the same card, one would be very straight forward while the other would have a **pink embellishment** or perhaps several. For example, if the scales of justice were used in the design, maybe the second version would have a pink flower about to bloom on the scale somewhere. Or maybe it's my logo that is different and pink.
While both designs have to be pretty conservative, I still want it to give off a sense that I'm alternative and think outside the box. With lawyers, I think a little bit of deviation goes a long way (less is more).
As far as colour goes (other than the pink embellishment), I was thinking something monochromatic, probably black and white but I am open to considering more colours. I personally love colour, and would love to use more colour, but am hesitant because of the nature of the profession. If you can find a way to use more colour while keeping it conservative and letting the pink pop, I'd be pretty pleased.
In general, I would prefer a clean simplistic design and logo. It should be immediately obvious that I'm a lawyer just by glancing at the card. I'm open to symbols of law, like the scales of justice or lady justice or something else. However, I don't want it to be the same as everyone else's.
Eventually, the design/style should be easy to recreate in the form of a website.
As far as the logo goes, it would probably use a circle as my last name starts with the letter "O". It can be very simple, with just my name and "Barrister & Solicitor". I don't currently have a logo, but the winning designer will be invited to provide a separate file for just the logo for an additional fee (I think it was CA$99). (Please ignore the uploaded logo file, it just wouldn't let me continue without uploading something).
As for the information that should go into the card, I'm still finalizing my address and phone number. So please use a placeholder for now.
Target Market(s)
Women, victims of sexual or domestic violence, refugees, people in need of legal services
Industry/Entity Type
Lawyer
Contact Information for Business Card
Marla Vent
Barrister & Solicitor
LL.B., B.C.L., B.F.A.
Criminal & Immigration Law
Street address
Toronto, ON
Postal Code
Phone number
Fax number
Email
Logo Text
Marla Vent, Barrister & Solicitor
Requirements
Must have
- Two versions
- One with pink
- Simplistic
Nice to have
- Maybe more colour
Should not have
- Not too conservative
- Not too predictable

```html
<!DOCTYPE html>
<html lang="en">
<head>
<meta charset="utf-8">
<title>Marla Vent — Business Cards</title>
<link rel="stylesheet" href="https://fonts.googleapis.com/css2?family=Questrial&display=swap">
<style>
  :root {
    --page: #ffffff;
    --card: #2b2e3a;
    --ink: #f2f2f4;
    --ink-soft: #a9adb6;
    --rule: #7c8486;
    --pink: #e43fe8;
    --plum: #8a35a0;
    --slate: #687977;
    --silver: #c9cdd0;
  }
  * { box-sizing: border-box; margin: 0; padding: 0; }
  html, body { width: 843px; height: 1200px; overflow: hidden; background: var(--page); }
  body { position: relative; font-family: "Questrial", Arial, sans-serif; }

  .card { position: absolute; width: 351px; height: 523px; background: var(--card); overflow: hidden; }
  .card--pink { --accent: var(--pink); --band: var(--plum); --orb: linear-gradient(160deg, var(--pink), #b7a3c0 70%, #9a9a9a); --wash: linear-gradient(180deg, rgba(120,60,150,.85), rgba(80,85,110,.75) 55%, rgba(75,80,100,.6)); }
  .card--classic { --accent: var(--silver); --band: var(--slate); --orb: linear-gradient(160deg, #9b9ea2, #f4f4f4 55%, #c2c4c6); --wash: linear-gradient(180deg, rgba(110,115,125,.8), rgba(95,100,112,.75)); }

  .front--pink { left: 37px; top: 42px; }
  .back--pink { left: 456px; top: 42px; }
  .front--classic { left: 37px; top: 638px; }
  .back--classic { left: 456px; top: 638px; }

  .band { position: absolute; left: 0; right: 0; bottom: 0; height: 39px; background: var(--band); }

  /* front */
  .logo-mark { position: absolute; left: 196px; top: 140px; width: 92px; height: 92px; border-radius: 50%; background: var(--orb); opacity: .9; }
  .logo-rule { position: absolute; left: 57px; width: 231px; height: 2px; background: var(--rule); }
  .logo-rule--top { top: 282px; }
  .logo-rule--bottom { top: 340px; }
  .logo-name { position: absolute; left: 57px; width: 231px; top: 292px; text-align: center; font-size: 33px; color: var(--ink); letter-spacing: 1px; line-height: 40px; }
  .logo-title { position: absolute; left: 57px; width: 231px; top: 352px; text-align: center; font-size: 16px; color: var(--ink-soft); letter-spacing: 1.3px; }

  /* back */
  .feather-wash { position: absolute; left: 222px; top: 76px; width: 126px; height: 408px; border-radius: 60% 40% 0 0 / 30% 20% 0 0; background: var(--wash); }
  .back-name { position: absolute; left: 27px; top: 30px; font-size: 40px; color: var(--ink); letter-spacing: 1px; line-height: 46px; }
  .credentials { position: absolute; left: 25px; top: 80px; font-size: 13px; color: var(--ink-soft); letter-spacing: 1.8px; }
  .practice { position: absolute; left: 25px; top: 124px; font-size: 16px; color: var(--ink); letter-spacing: 1.6px; }

  .contact { position: absolute; left: 27px; display: flex; align-items: flex-start; color: var(--ink-soft); font-size: 13.5px; letter-spacing: 1.6px; }
  .contact svg { width: 28px; height: 22px; flex: none; color: var(--accent); }
  .contact span { display: block; }
  .contact--address { top: 209px; }
  .contact--address .lines { margin-left: 24px; line-height: 29.5px; margin-top: -3px; }
  .contact--phone { top: 320px; }
  .contact--fax { top: 370px; }
  .contact--email { top: 419px; }
  .contact--phone .value, .contact--fax .value, .contact--email .value { margin-left: 22px; line-height: 20px; }
</style>
</head>
<body>

<!-- Pink edition -->
<section class="card card--pink front--pink" aria-label="Card front, pink edition">
  <div class="logo-mark" aria-hidden="true"></div>
  <div class="logo-rule logo-rule--top"></div>
  <div class="logo-name">Marla Vent</div>
  <div class="logo-rule logo-rule--bottom"></div>
  <div class="logo-title">Barrister &amp; Solicitor</div>
  <div class="band"></div>
</section>

<section class="card card--pink back--pink" aria-label="Card back, pink edition">
  <div class="feather-wash" role="img" aria-label="Large faint quill feather decoration"></div>
  <div class="back-name">Marla Vent</div>
  <div class="credentials">LL.B., B.C.L., B.F.A.</div>
  <div class="practice">Criminal &amp; Immigration Law</div>
  <div class="contact contact--address">
    <svg viewBox="0 0 28 22"><rect x="1" y="2" width="26" height="17" fill="currentColor"/><path d="M1 2 L14 12 L27 2 M1 19 L11 10 M27 19 L17 10" stroke="#2b2e3a" stroke-width="1.6" fill="none"/></svg>
    <div class="lines"><span>Street address</span><span>Toronto, ON</span><span>Postal Code</span></div>
  </div>
  <div class="contact contact--phone">
    <svg viewBox="0 0 28 22"><ellipse cx="10" cy="9" rx="9" ry="7" fill="currentColor"/><path d="M4 14 L2 19 L8 15Z" fill="currentColor"/><ellipse cx="19" cy="13" rx="8" ry="6" fill="none" stroke="currentColor" stroke-width="1.6"/><circle cx="16" cy="13" r="1.2" fill="currentColor"/><circle cx="19.5" cy="13" r="1.2" fill="currentColor"/><circle cx="23" cy="13" r="1.2" fill="currentColor"/></svg>
    <span class="value">+00 000 000 0000</span>
  </div>
  <div class="contact contact--fax">
    <svg viewBox="0 0 28 22"><rect x="8" y="1" width="12" height="7" fill="none" stroke="currentColor" stroke-width="1.6"/><rect x="3" y="7" width="22" height="11" rx="3" fill="currentColor"/><rect x="8" y="13" width="12" height="8" fill="#2b2e3a" stroke="currentColor" stroke-width="1.4"/><path d="M10 16 H18 M10 18.5 H18" stroke="currentColor" stroke-width="1"/></svg>
    <span class="value">+00 000 000 0000</span>
  </div>
  <div class="contact contact--email">
    <svg viewBox="0 0 28 22"><circle cx="13" cy="11" r="10" fill="currentColor"/><text x="13" y="16" text-anchor="middle" font-size="15" font-family="Arial, sans-serif" fill="#ffffff">@</text></svg>
    <span class="value">email@email.com</span>
  </div>
  <div class="band"></div>
</section>

<!-- Classic edition -->
<section class="card card--classic front--classic" aria-label="Card front, classic edition">
  <div class="logo-mark" aria-hidden="true"></div>
  <div class="logo-rule logo-rule--top"></div>
  <div class="logo-name">Marla Vent</div>
  <div class="logo-rule logo-rule--bottom"></div>
  <div class="logo-title">Barrister &amp; Solicitor</div>
  <div class="band"></div>
</section>

<section class="card card--classic back--classic" aria-label="Card back, classic edition">
  <div class="feather-wash" role="img" aria-label="Large faint quill feather decoration"></div>
  <div class="back-name">Marla Vent</div>
  <div class="credentials">LL.B., B.C.L., B.F.A.</div>
  <div class="practice">Criminal &amp; Immigration Law</div>
  <div class="contact contact--address">
    <svg viewBox="0 0 28 22"><rect x="1" y="2" width="26" height="17" fill="currentColor"/><path d="M1 2 L14 12 L27 2 M1 19 L11 10 M27 19 L17 10" stroke="#2b2e3a" stroke-width="1.6" fill="none"/></svg>
    <div class="lines"><span>Street address</span><span>Toronto, ON</span><span>Postal Code</span></div>
  </div>
  <div class="contact contact--phone">
    <svg viewBox="0 0 28 22"><ellipse cx="10" cy="9" rx="9" ry="7" fill="currentColor"/><path d="M4 14 L2 19 L8 15Z" fill="currentColor"/><ellipse cx="19" cy="13" rx="8" ry="6" fill="none" stroke="currentColor" stroke-width="1.6"/><circle cx="16" cy="13" r="1.2" fill="currentColor"/><circle cx="19.5" cy="13" r="1.2" fill="currentColor"/><circle cx="23" cy="13" r="1.2" fill="currentColor"/></svg>
    <span class="value">+00 000 000 0000</span>
  </div>
  <div class="contact contact--fax">
    <svg viewBox="0 0 28 22"><rect x="8" y="1" width="12" height="7" fill="none" stroke="currentColor" stroke-width="1.6"/><rect x="3" y="7" width="22" height="11" rx="3" fill="currentColor"/><rect x="8" y="13" width="12" height="8" fill="#2b2e3a" stroke="currentColor" stroke-width="1.4"/><path d="M10 16 H18 M10 18.5 H18" stroke="currentColor" stroke-width="1"/></svg>
    <span class="value">+00 000 000 0000</span>
  </div>
  <div class="contact contact--email">
    <svg viewBox="0 0 28 22"><circle cx="13" cy="11" r="10" fill="currentColor"/><text x="13" y="16" text-anchor="middle" font-size="15" font-family="Arial, sans-serif" fill="#2b2e3a">@</text></svg>
    <span class="value">email@email.com</span>
  </div>
  <div class="band"></div>
</section>

</body>
</html>
```